Business Card Design Project - del varosi group

dear Sirs

we need business card design for our group ( DEL Varosi Group ) , i have got the Logo design of our group from pixel harbor in previous , so all need details relating to our group i think available with you, as well as the the chosen logo design

we hope to provide us with business card logo that to be appropaite and satisfactory to us .

thanks

note : logo design of our group is attached .
Updates

Reason: please extend the deadline of my project for additional 15 days because i didn't received appropriate design for our gruop yet . kindly beaware that i have received 77 design till now , supossed to send me 200-250 design at least . thanks

Target Market(s)

contents

name : Kerem EL Nadiri

position : Operation Manager

Industry/Entity Type

Business

Requirements
Must have

• person name

group logo
Nice to have
• logo color matching with back background

```html
<!DOCTYPE html>
<html lang="en">
<head>
<meta charset="utf-8">
<title>DEL Varosi Group – Business Card</title>
<link rel="stylesheet" href="https://fonts.googleapis.com/css2?family=Source+Sans+3:wght@400;600;700&display=swap">
<style>
  :root {
    --stage: #b38a25;
    --card-white: #ffffff;
    --brand-blue: #0f4f8f;
    --accent-blue: #1a74bb;
    --accent-gold: #c7962f;
    --ink: #1b1b1b;
    --back-light: #3d8fcb;
    --back-dark: #0d4f8f;
  }
  * { box-sizing: border-box; margin: 0; padding: 0; }
  html, body {
    width: 1200px; height: 686px; overflow: hidden;
    background: var(--stage);
    font-family: "Source Sans 3", "Myriad Pro", Arial, sans-serif;
  }
  .stage { position: relative; width: 1200px; height: 686px; }

  .card {
    position: absolute; width: 524px; height: 299px;
    box-shadow: 1px 2px 4px rgba(0,0,0,.45);
  }
  .card--front { left: 55px; top: 156px; background: var(--card-white); }
  .card--back {
    left: 612px; top: 241px;
    background: radial-gradient(ellipse at 50% 45%, var(--back-light) 0%, var(--accent-blue) 45%, var(--back-dark) 100%);
  }

  .wordmark {
    position: absolute; left: 0; right: 0;
    display: flex; align-items: center; justify-content: center; gap: 10px;
    font-weight: 700; letter-spacing: .5px; text-transform: uppercase;
  }
  .wordmark__square { width: 18px; height: 18px; }
  .card--front .wordmark { top: 70px; font-size: 36px; color: var(--brand-blue); }
  .card--front .wordmark__square { background: var(--brand-blue); }
  .card--back .wordmark { top: 112px; font-size: 40px; color: #fff; }
  .card--back .wordmark__square { background: #fff; }

  .divider {
    position: absolute; left: 168px; width: 188px; top: 157px; height: 2px;
    background: linear-gradient(90deg, rgba(0,0,0,0), #222 50%, rgba(0,0,0,0));
  }

  .edge-tab { position: absolute; top: 126px; height: 57px; width: 15px; }
  .edge-tab--left { left: 0; border-left: 12px solid var(--accent-blue); }
  .edge-tab--left::after { content: ""; position: absolute; right: -3px; top: 0; width: 3px; height: 100%; background: var(--accent-gold); }
  .edge-tab--right { right: 0; border-right: 12px solid var(--accent-blue); }
  .edge-tab--right::after { content: ""; position: absolute; left: -3px; top: 0; width: 3px; height: 100%; background: var(--accent-gold); }

  .identity {
    position: absolute; left: 0; right: 0; top: 174px;
    display: flex; justify-content: center; align-items: baseline; gap: 8px;
  }
  .identity__name { font-size: 15.5px; font-weight: 700; color: var(--accent-blue); }
  .identity__sep { width: 1px; height: 13px; background: #555; align-self: center; }
  .identity__role { font-size: 13px; font-weight: 700; color: var(--accent-gold); }

  .contact-row {
    position: absolute; left: 0; right: 0;
    display: flex; justify-content: center; gap: 14px;
    font-size: 13px; color: var(--ink);
  }
  .contact-row--phones { top: 202px; }
  .contact-row--web { top: 220px; }
  .contact-row--address { top: 240px; }
  .contact-item { display: inline-flex; align-items: center; gap: 2px; }
  .contact-item svg { width: 11px; height: 11px; fill: var(--accent-blue); }
</style>
</head>
<body>
<main class="stage">

  <section class="card card--front" aria-label="Business card front">
    <div class="wordmark"><span class="wordmark__square"></span>DEL Varosi Group</div>
    <div class="divider"></div>
    <span class="edge-tab edge-tab--left"></span>
    <span class="edge-tab edge-tab--right"></span>

    <div class="identity">
      <span class="identity__name">Kerem EL Nadiri</span>
      <span class="identity__sep"></span>
      <span class="identity__role">Operation Manager</span>
    </div>

    <div class="contact-row contact-row--phones">
      <span class="contact-item">
        <svg viewBox="0 0 24 24"><path d="M6.6 10.8a15.1 15.1 0 0 0 6.6 6.6l2.2-2.2c.3-.3.7-.4 1-.2 1.1.4 2.3.6 3.6.6.6 0 1 .4 1 1V20c0 .6-.4 1-1 1A17 17 0 0 1 3 4c0-.6.4-1 1-1h3.5c.6 0 1 .4 1 1 0 1.3.2 2.5.6 3.6.1.3 0 .7-.2 1z"/></svg>(TF)123-456-7890
      </span>
      <span class="contact-item">
        <svg viewBox="0 0 24 24"><path d="M6.6 10.8a15.1 15.1 0 0 0 6.6 6.6l2.2-2.2c.3-.3.7-.4 1-.2 1.1.4 2.3.6 3.6.6.6 0 1 .4 1 1V20c0 .6-.4 1-1 1A17 17 0 0 1 3 4c0-.6.4-1 1-1h3.5c.6 0 1 .4 1 1 0 1.3.2 2.5.6 3.6.1.3 0 .7-.2 1z"/></svg>123-456-7890
      </span>
      <span class="contact-item">
        <svg viewBox="0 0 24 24"><path d="M6 2h12v6H6zM4 9h16a2 2 0 0 1 2 2v6h-4v5H6v-5H2v-6a2 2 0 0 1 2-2zm4 8v3h8v-3z"/></svg>123-456-7890
      </span>
    </div>

    <div class="contact-row contact-row--web">
      <span class="contact-item">
        <svg viewBox="0 0 24 24"><path d="M2 5h20v14H2zm2 2v.5l8 5 8-5V7z"/></svg>name@website.com
      </span>
      <span class="contact-item">
        <svg viewBox="0 0 24 24"><path d="M12 2a10 10 0 1 0 0 20 10 10 0 0 0 0-20zm6.9 6h-3a15 15 0 0 0-1.3-3.6A8 8 0 0 1 18.9 8zM12 4c.8 1.2 1.5 2.5 1.9 4h-3.8c.4-1.5 1.1-2.8 1.9-4zM4.3 14a8 8 0 0 1 0-4h3.4a16 16 0 0 0 0 4zm.8 2h3a15 15 0 0 0 1.3 3.6A8 8 0 0 1 5.1 16zm3-8h-3a8 8 0 0 1 4.3-3.6C8.8 5.5 8.4 6.7 8.1 8zM12 20c-.8-1.2-1.5-2.5-1.9-4h3.8c-.4 1.5-1.1 2.8-1.9 4zm2.3-6H9.7a14 14 0 0 1 0-4h4.6a14 14 0 0 1 0 4zm.3 5.6c.6-1.1 1-2.3 1.3-3.6h3a8 8 0 0 1-4.3 3.6zm1.7-5.6a16 16 0 0 0 0-4h3.4a8 8 0 0 1 0 4z"/></svg>www.website.com
      </span>
    </div>

    <div class="contact-row contact-row--address">
      <span>Street name City, State, zip code</span>
    </div>
  </section>

  <section class="card card--back" aria-label="Business card back">
    <div class="wordmark"><span class="wordmark__square"></span>DEL Varosi Group</div>
  </section>

</main>
</body>
</html>
```